Lorvex Tilo medical cannibis cultivation company

tag - Tilo rise
Lorvex Tilo medical cannabis cultivation - logo is selected- can we please see bold examples with our selection. We are mainly dealing with medical companies and professionals. We would like to be stand out in the crowd with our designs. Welcome any and all attempts. Thanks

Target Market(s)

Medical and Professional

Industry/Entity Type

Medical And Science

Font styles to use
Sans Serif

Colors

Designer to choose colors to be used in the design.

Requirements
Must have
• Bright colour and be bold- Love the teal and magenta that is currently on the dark background design.
Nice to have
• shading and the 3D affect- The shadowed appearance.
Should not have
• Anything related to illegal activity or un professional manners

```html
<!DOCTYPE html>
<html lang="en">
<head>
<meta charset="utf-8">
<title>Lorvex Tilo business card</title>
<link href="https://fonts.googleapis.com/css2?family=Roboto:wght@300;400;500;700&display=swap" rel="stylesheet">
<style>
  :root {
    --backdrop: #ece8e3;
    --paper: #ffffff;
    --magenta: #9b479c;
    --teal: #1aaee6;
    --ink: #3a3a3a;
    --rule: #c9c9c9;
    --white: #ffffff;
  }
  * { box-sizing: border-box; margin: 0; padding: 0; }
  html, body { width: 1200px; height: 1040px; overflow: hidden; }
  body {
    background: var(--backdrop);
    font-family: "Roboto", sans-serif;
    position: relative;
  }
  .card {
    position: absolute;
    width: 600px;
    height: 343px;
    border-radius: 22px;
    overflow: hidden;
    box-shadow: 0 14px 30px rgba(60, 40, 30, 0.25), 0 2px 5px rgba(60, 40, 30, 0.2);
  }
  .card-front { left: 300px; top: 110px; background: var(--paper); }
  .card-back { left: 300px; top: 560px; background: var(--magenta); }

  /* front */
  .brand-lockup {
    position: absolute; right: 46px; top: 36px;
    display: flex; align-items: center; gap: 14px;
  }
  .brand-dot {
    width: 58px; height: 58px; border-radius: 50%;
    border: 3px solid var(--rule);
  }
  .brand-text { display: flex; flex-direction: column; align-items: flex-end; }
  .brand-name {
    font-size: 30px; font-weight: 500; color: var(--teal);
    letter-spacing: 1px; text-transform: uppercase; line-height: 1;
  }
  .brand-tag {
    font-size: 11px; font-weight: 400; color: #8a8a8a;
    letter-spacing: 2px; text-transform: uppercase; margin-top: 5px;
    border-top: 1px solid var(--rule); padding-top: 3px;
  }
  .divider {
    position: absolute; left: 40px; right: 40px; top: 170px;
    height: 1px; background: var(--rule);
  }
  .person { position: absolute; left: 40px; top: 110px; }
  .person-name {
    font-size: 26px; font-weight: 500; color: var(--teal);
    text-transform: uppercase; line-height: 1;
  }
  .person-role {
    font-size: 15px; color: var(--magenta); text-transform: uppercase; margin-top: 5px;
  }
  .contacts { position: absolute; left: 40px; top: 184px; list-style: none; }
  .contacts li {
    display: flex; align-items: center; gap: 10px;
    font-size: 14px; color: var(--ink); line-height: 22px;
  }
  .contacts svg { width: 13px; height: 13px; fill: var(--teal); flex: none; }
  .address {
    position: absolute; right: 46px; top: 196px; text-align: right;
    font-size: 14px; color: var(--ink); line-height: 21px;
  }
  .band { position: absolute; left: 0; right: 0; bottom: 0; height: 40px; }
  .band svg { display: block; width: 100%; height: 100%; }
  .band-url {
    position: absolute; right: 46px; bottom: 11px;
    font-size: 13px; color: var(--white); letter-spacing: 0.3px;
  }

  /* back */
  .back-lockup {
    position: absolute; right: 48px; bottom: 52px;
    display: flex; flex-direction: column; align-items: flex-end;
  }
  .back-name {
    font-size: 54px; font-weight: 500; color: var(--white);
    text-transform: uppercase; letter-spacing: 1px; line-height: 1;
  }
  .back-tag {
    font-size: 16px; color: var(--white); text-transform: uppercase;
    letter-spacing: 3px; margin-top: 6px;
    border-top: 1px solid var(--white); padding-top: 4px;
  }
  .back-url {
    font-size: 13px; color: var(--white); letter-spacing: 6px; margin-top: 10px;
  }
</style>
</head>
<body>
  <section class="card card-front">
    <div class="brand-lockup">
      <span class="brand-dot"></span>
      <div class="brand-text">
        <span class="brand-name">Lorvex Tilo</span>
        <span class="brand-tag">Tilo rise</span>
      </div>
    </div>

    <div class="person">
      <p class="person-name">Mara Ellison</p>
      <p class="person-role">CEO/Founder</p>
    </div>

    <div class="divider"></div>

    <ul class="contacts">
      <li><svg viewBox="0 0 24 24"><path d="M6.6 10.8a15.1 15.1 0 0 0 6.6 6.6l2.2-2.2a1 1 0 0 1 1-.25 11.4 11.4 0 0 0 3.6.57 1 1 0 0 1 1 1V20a1 1 0 0 1-1 1A17 17 0 0 1 3 4a1 1 0 0 1 1-1h3.5a1 1 0 0 1 1 1c0 1.25.2 2.45.57 3.57a1 1 0 0 1-.25 1z"/></svg>907 214 5580</li>
      <li><svg viewBox="0 0 24 24"><path d="M7 2h10a2 2 0 0 1 2 2v16a2 2 0 0 1-2 2H7a2 2 0 0 1-2-2V4a2 2 0 0 1 2-2zm0 3v13h10V5z"/></svg>907 381 6627</li>
      <li><svg viewBox="0 0 24 24"><path d="M6 2h12v6H6zM4 9h16a2 2 0 0 1 2 2v7h-4v4H6v-4H2v-7a2 2 0 0 1 2-2zm4 8v3h8v-3z"/></svg>907 455 1093</li>
      <li><svg viewBox="0 0 24 24"><path d="M2 5h20v14H2zm2 2v.5l8 5 8-5V7z"/></svg>mara@lorvextilo.com</li>
    </ul>

    <p class="address">4120 Alder Row<br>Juneau, Alaska 99801</p>

    <div class="band">
      <svg viewBox="0 0 600 40" preserveAspectRatio="none">
        <polygon points="0,0 370,0 355,40 0,40" fill="var(--magenta)"/>
        <polygon points="376,0 600,0 600,40 361,40" fill="var(--teal)"/>
        <polygon points="370,0 376,0 361,40 355,40" fill="var(--white)"/>
      </svg>
      <span class="band-url">www.lorvextilo.com</span>
    </div>
  </section>

  <section class="card card-back">
    <div class="back-lockup">
      <span class="back-name">Lorvex Tilo</span>
      <span class="back-tag">Tilo rise</span>
      <span class="back-url">www.lorvextilorise.com</span>
    </div>
  </section>
</body>
</html>
```